Custom unique Stationary design for Logistics company

We need a custom, unique , elegant and luxurious full stationary design using our new logo, following these guidelines:
1- Business card: double sided, both sides uses the navy blue as the background main color (same as the code of the navy blue used in our logo).
2- envelope and folder: also use the same navy blue as the main background color.
3- book cover( notepad cover) : same thing with the navy blue
4- letterhead: feel free to use the combination of the colors in our logo.
5- rest of the items are up to your creativity

Target Market(s)

corporates and other businesses

Industry/Entity Type

Logistics and heavy machines contractors

Requirements
Must have
• Letterhead, business card, envelope, notepad cover, paper, file
Nice to have
• navy blue to be main background color for business card, envelope, notepad cover

```html
<!DOCTYPE html>
<html lang="en">
<head>
<meta charset="utf-8">
<title>Northway Freight Group – Letterhead</title>
<link href="https://fonts.googleapis.com/css2?family=Lato:wght@400;700&family=Allura&display=swap" rel="stylesheet">
<style>
  :root {
    --navy: #0b4a73;
    --orange: #e35a28;
    --ink: #2f2f2f;
    --paper: #ffffff;
    --backdrop: #e4e4e4;
  }
  * { box-sizing: border-box; margin: 0; padding: 0; }
  html, body { width: 1200px; height: 960px; overflow: hidden; }
  body {
    background: var(--backdrop);
    font-family: "Lato", Arial, sans-serif;
    color: var(--ink);
    position: relative;
  }
  .letterhead {
    position: absolute;
    left: 282px; top: 30px;
    width: 636px; height: 900px;
    background: var(--paper);
    box-shadow: 0 4px 18px rgba(0,0,0,.12);
    overflow: hidden;
  }
  .brand {
    position: absolute; left: 48px; top: 96px;
    display: flex; align-items: center; gap: 8px;
  }
  .brand-dot { width: 12px; height: 12px; border-radius: 50%; background: var(--orange); }
  .brand-name { font-weight: 700; font-size: 19px; color: var(--navy); letter-spacing: .3px; }
  .head-rule {
    position: absolute; left: 104px; top: 146px;
    width: 482px; height: 2px; background: var(--navy);
  }
  .contact {
    position: absolute; left: 400px; top: 52px;
    height: 94px;
    padding-left: 12px; border-left: 1px solid var(--navy);
    font-size: 9.5px; line-height: 13px; color: var(--ink);
    font-style: normal;
  }
  .contact .addr { margin-bottom: 3px; }
  .contact-line { display: flex; align-items: center; gap: 5px; }
  .contact-line svg { width: 8px; height: 8px; fill: var(--navy); }
  .letter {
    position: absolute; left: 104px; top: 196px; width: 470px;
    font-size: 10.8px; line-height: 14.5px; color: var(--ink);
  }
  .date { margin-bottom: 16px; font-size: 12px; }
  .recipient { margin-bottom: 14px; font-size: 12px; line-height: 15px; }
  .company { margin-bottom: 16px; font-size: 12px; line-height: 15px; }
  .salutation { font-weight: 700; font-size: 14px; margin-bottom: 12px; }
  .letter p.body { margin-bottom: 14px; }
  .closing { margin-top: 24px; font-size: 11px; line-height: 14px; }
  .signature {
    display: block;
    font-family: "Allura", cursive;
    font-size: 40px; line-height: 44px; color: var(--ink);
    margin-top: 10px; margin-left: 26px;
  }
  .wave { position: absolute; left: 0; bottom: 0; width: 636px; height: 240px; }
</style>
</head>
<body>
  <main class="letterhead">
    <div class="brand">
      <span class="brand-dot"></span>
      <span class="brand-name">Northway Freight Group</span>
    </div>

    <address class="contact">
      <div class="addr">4120 Harbour Line, Unit 18<br>Fairport, ON K2M 4B7</div>
      <div class="contact-line">
        <svg viewBox="0 0 10 10"><path d="M2 0h2l1 3-1.5 1a6 6 0 0 0 2.5 2.5L7 5l3 1v2a2 2 0 0 1-2 2A8 8 0 0 1 0 2a2 2 0 0 1 2-2z"/></svg>
        014 382 7160
      </div>
      <div class="contact-line">
        <svg viewBox="0 0 10 10"><path d="M0 2h10v6H0z M0 2l5 3.5L10 2" fill="none" stroke="#0b4a73" stroke-width="1.2"/></svg>
        hello@northwayfreight.com
      </div>
      <div class="contact-line">
        <svg viewBox="0 0 10 10"><circle cx="5" cy="5" r="4.5"/></svg>
        www.northwayfreight.com
      </div>
    </address>

    <div class="head-rule"></div>

    <section class="letter">
      <div class="date">January-03-2020</div>
      <div class="recipient">Mr. Alan Reeve<br>President</div>
      <div class="company">Crestline Holdings<br>48 Market Avenue, Suite# 10<br>City, State, 120023</div>
      <div class="salutation">Dear Mr. Reeve</div>
      <p class="body">Lorem ipsum dolor sit amet, consectetur adipisicing elit, sed do eiusmod tempor incididunt ut labore et dolore magna aliqua. Ut enim ad minim veniam, quis nostrud exercitation ullamco laboris nisi ut aliquip ex ea commodo consequat. Duis aute irure dolor in reprehenderit in voluptate velit esse cillum dolore eu fugiat nulla pariatur.</p>
      <p class="body">Lorem ipsum dolor sit amet, consectetur adipisicing elit, sed do eiusmod tempor incididunt ut labore et dolore magna aliqua. Ut enim ad minim veniam, quis nostrud exercitation ullamco laboris nisi ut aliquip ex ea commodo consequat. Duis aute irure dolor in reprehenderit in voluptate velit esse cillum dolore eu fugiat nulla pariatur.</p>
      <p class="body">Lorem ipsum dolor sit amet, consectetur adipisicing elit, sed do eiusmod tempor incididunt ut labore et dolore magna aliqua. Ut enim ad minim veniam, quis nostrud exercitation ullamco laboris nisi ut aliquip ex ea commodo consequat.</p>
      <p class="body">Excepteur sint occaecat cupidatat non proident, sunt in culpa qui officia deserunt mollit anim id est laborum. re et dolore magnam aliquam quaerat voluptatem.</p>
      <div class="closing">Regards</div>
      <div class="signature">Daniel Hart</div>
    </section>

    <svg class="wave" viewBox="0 0 636 240" preserveAspectRatio="none" aria-hidden="true">
      <path d="M0 206 C120 200 230 180 320 120 C410 58 520 20 636 12 L636 18 C525 28 420 68 332 128 C240 192 130 216 0 222 Z" fill="var(--orange)"/>
      <path d="M0 232 C140 226 250 202 342 140 C430 80 530 44 636 38 L636 240 L0 240 Z" fill="var(--navy)"/>
    </svg>
  </main>
</body>
</html>
```